New LLC consulting company needs a business card design

I need a business card design for new company in Alexandria Virginia called TK Verdane Consulting LLC. The company is focused on consulting for defense and national security issues with expertise in nuclear and space topics. I would like to see designs that are simple and I am open to colors except for brown.

Target Market(s)

All businesses that are seeking consulting help

Industry/Entity Type

Consulting

Contact Information for Business Card

Name of company - TK Verdane Consulting LLC; name (Delia Pratt) President; email: prattdq47@mailvessa.com; Phone: 703-555-0142

Requirements
Must have
• The details described above
Nice to have
• I'm open to all ideas
Should not have
• No brown

```html
<!DOCTYPE html>
<html lang="en">
<head>
<meta charset="utf-8">
<title>Delia Pratt — TK Verdane Consulting LLC</title>
<link href="https://fonts.googleapis.com/css2?family=Montserrat:wght@400;700&display=swap" rel="stylesheet">
<style>
  :root {
    --backdrop: #999999;
    --card-navy: #073c60;
    --ink-light: #ffffff;
  }
  html, body {
    margin: 0;
    padding: 0;
    width: 1200px;
    height: 1059px;
    overflow: hidden;
    background: var(--backdrop);
  }
  .canvas {
    position: relative;
    width: 1200px;
    height: 1059px;
  }
  .business-card {
    position: absolute;
    left: 234px;
    top: 320px;
    width: 733px;
    height: 419px;
    border-radius: 26px;
    background: var(--card-navy);
    color: var(--ink-light);
    font-family: "Montserrat", sans-serif;
  }
  .company-name {
    position: absolute;
    left: 38px;
    top: 58px;
    margin: 0;
    font-size: 19px;
    font-weight: 400;
    line-height: 1;
    letter-spacing: 0.6px;
  }
  .person-name {
    position: absolute;
    left: 38px;
    top: 125px;
    margin: 0;
    font-size: 37px;
    font-weight: 700;
    line-height: 1;
    letter-spacing: 0.2px;
  }
  .person-title {
    position: absolute;
    left: 38px;
    top: 174px;
    margin: 0;
    font-size: 19px;
    font-weight: 400;
    line-height: 1;
    letter-spacing: 0.6px;
  }
  .divider {
    position: absolute;
    left: 39px;
    top: 213px;
    width: 655px;
    height: 1.5px;
    background: var(--ink-light);
  }
  .contact-list {
    position: absolute;
    left: 38px;
    top: 235px;
    margin: 0;
    padding: 0;
    list-style: none;
  }
  .contact-item {
    display: flex;
    align-items: center;
    height: 34px;
    font-size: 18.5px;
    font-weight: 400;
    letter-spacing: 0.5px;
    line-height: 1;
  }
  .contact-icon {
    width: 16px;
    height: 16px;
    margin-right: 9px;
    flex: none;
    fill: var(--ink-light);
  }
</style>
</head>
<body>
<div class="canvas">
  <div class="business-card">
    <p class="company-name">TK Verdane Consulting LLC</p>
    <h1 class="person-name">Delia Pratt</h1>
    <p class="person-title">President</p>
    <div class="divider"></div>
    <ul class="contact-list">
      <li class="contact-item">
        <svg class="contact-icon" viewBox="0 0 16 16" aria-hidden="true">
          <path d="M1 4h14v9H1z" />
          <path d="M1 4l7 5 7-5" fill="none" stroke="#073c60" stroke-width="1.3"/>
          <path d="M1 13l5-4M15 13l-5-4" fill="none" stroke="#073c60" stroke-width="1.1"/>
        </svg>
        <span>prattdq47@mailvessa.com</span>
      </li>
      <li class="contact-item">
        <svg class="contact-icon" viewBox="0 0 16 16" aria-hidden="true">
          <path d="M3.6 1.5l2.3 2.9-1.4 1.6c.9 2 2.4 3.5 4.4 4.5l1.6-1.4 2.9 2.3-1.6 2.4C6.9 13.6 2.4 9.1 1.2 3.1z"/>
          <path d="M9 3.2a4 4 0 0 1 3.8 3.8M9.2 0.9a6.2 6.2 0 0 1 5.9 5.9" fill="none" stroke="#ffffff" stroke-width="1.3"/>
        </svg>
        <span>703-555-0142</span>
      </li>
    </ul>
  </div>
</div>
</body>
</html>
```